Upscale business cards needed for Board of Directors

We need professional business cards created for members of our family business Board of Directors. We would like these relatively simple and straightforward, but also with a unique element to set them apart. Probably stick with neutral and simple colors - white, grey etc. We need space for the traditional elements, including name, title, address, email/phone number. And we will be creating several from this template so it needs to be template that is easy to switch information in and out of.
Business
See description

```html
<!DOCTYPE html>
<html lang="en">
<head>
<meta charset="utf-8">
<title>Harbormark Holdings – Business Cards</title>
<link rel="stylesheet" href="https://fonts.googleapis.com/css2?family=Arimo:wght@400;700&display=swap">
<style>
  :root {
    --backdrop: #e6e4e1;
    --card: #141414;
    --card-edge: #1d1d1d;
    --white: #f4f4f4;
    --silver: #bdbdbd;
    --muted: #8a8a8a;
    --gold: #b39a6e;
    --text-font: "Arimo", Arial, sans-serif;
  }
  * { box-sizing: border-box; margin: 0; padding: 0; }
  html, body { width: 1200px; height: 864px; overflow: hidden; }
  body {
    background: var(--backdrop);
    font-family: var(--text-font);
    position: relative;
  }
  .card {
    position: absolute;
    width: 525px;
    height: 300px;
    background: var(--card);
    border: 1px solid var(--card-edge);
    box-shadow: 0 14px 30px rgba(0,0,0,.25);
  }
  .card--back { left: 50px; top: 150px; }
  .card--front { left: 625px; top: 414px; }

  /* Brand name set as plain text */
  .brand {
    font-family: var(--text-font);
    font-weight: 700;
    color: var(--white);
    text-transform: uppercase;
    line-height: 1.05;
    text-align: center;
  }
  .brand__line { display: block; font-size: 34px; letter-spacing: 1px; }
  .brand__line--sub { font-size: 20px; letter-spacing: 7px; margin-top: 4px; }

  .card--back .brand { position: absolute; left: 0; right: 0; top: 96px; color: var(--silver); }
  .back__web {
    position: absolute; left: 0; right: 0; top: 205px;
    text-align: center; font-size: 13px; letter-spacing: 4px; color: var(--muted);
  }

  .card--front .brand { position: absolute; left: 28px; width: 250px; top: 118px; }
  .front__divider {
    position: absolute; left: 300px; top: 60px; width: 1px; height: 180px;
    background: linear-gradient(to bottom, rgba(255,255,255,0), rgba(255,255,255,.75) 50%, rgba(255,255,255,0));
  }
  .contact { position: absolute; left: 320px; top: 66px; color: var(--white); }
  .contact__name { color: var(--gold); font-size: 17px; font-weight: 700; }
  .contact__title { font-size: 15px; margin-top: 3px; }
  .contact__address { font-size: 12.5px; line-height: 1.35; margin-top: 12px; }
  .contact__list { list-style: none; margin-top: 10px; font-size: 12.5px; }
  .contact__list li { display: flex; align-items: center; gap: 9px; margin-bottom: 5px; }
  .contact__icon { width: 13px; height: 13px; fill: var(--gold); flex: none; }
</style>
</head>
<body>

<section class="card card--back" aria-label="Card back">
  <div class="brand">
    <span class="brand__line">Harbormark</span>
    <span class="brand__line brand__line--sub">Holdings</span>
  </div>
  <p class="back__web">www.harbormark.com</p>
</section>

<section class="card card--front" aria-label="Card front">
  <div class="brand">
    <span class="brand__line">Harbormark</span>
    <span class="brand__line brand__line--sub">Holdings</span>
  </div>
  <div class="front__divider"></div>
  <div class="contact">
    <p class="contact__name">Peter Vance</p>
    <p class="contact__title">President</p>
    <p class="contact__address">2170 Linden Crest Road<br>Maple Grove, NY 11020</p>
    <ul class="contact__list">
      <li>
        <svg class="contact__icon" viewBox="0 0 16 16" aria-hidden="true"><path d="M3.6 1.2l2.2 2.6c.4.5.3 1.1-.1 1.5L4.6 6.4c.8 1.9 2.3 3.4 4.9 5l1.1-1.1c.4-.4 1-.5 1.5-.1l2.6 2.2c.5.4.5 1.1.1 1.5l-1.2 1.2C11.6 17 1 7.9 1.9 3.3L3.1 1.6c.1-.2.3-.4.5-.4z"/></svg>
        <span>555 0148 2290</span>
      </li>
      <li>
        <svg class="contact__icon" viewBox="0 0 16 16" aria-hidden="true"><path d="M1 3h14v10H1z M2 4.2v.4l6 4 6-4v-.4z" fill-rule="evenodd"/></svg>
        <span>peter@harbormark.com</span>
      </li>
      <li>
        <svg class="contact__icon" viewBox="0 0 16 16" aria-hidden="true"><path d="M8 1a5 5 0 0 0-5 5c0 3.6 5 9 5 9s5-5.4 5-9a5 5 0 0 0-5-5zm0 7a2 2 0 1 1 0-4 2 2 0 0 1 0 4z"/></svg>
        <span>www.harbormark.com</span>
      </li>
    </ul>
  </div>
</section>

</body>
</html>
```